Brellwick Partners, LLC Stationary

Brellwick Partners, LLC is a new financial planning and consulting company. We are looking for designs on business cards, letterhead, envelopes, and anything else that would be useful. Our preference for business card design is two sided. We are looking for a professional and clean look with incorporating the logo and patriotic feel. Thank you to all who participate and good luck!

```html
<!DOCTYPE html>
<html lang="en">
<head>
<meta charset="utf-8">
<title>Brellwick Partners, LLC Stationery</title>
<link href="https://fonts.googleapis.com/css2?family=Arimo:wght@400;600&display=swap" rel="stylesheet">
<style>
  :root {
    --navy: #103d6b;
    --red: #c3202a;
    --paper: #f5f4f2;
    --ink: #4a4a4a;
    --backdrop: #a9a7a8;
  }
  * { margin: 0; padding: 0; box-sizing: border-box; }
  html, body { width: 1200px; height: 770px; overflow: hidden; }
  body {
    position: relative;
    background: var(--backdrop);
    font-family: "Arimo", Arial, sans-serif;
    color: var(--ink);
  }
  .piece {
    position: absolute;
    background: var(--paper);
    box-shadow: 0 2px 6px rgba(0,0,0,.25);
    overflow: hidden;
  }
  .piece svg.decor { position: absolute; inset: 0; }
  .brand { position: absolute; display: flex; align-items: center; gap: 6px; }
  .brand-dot { border-radius: 50%; background: var(--red); flex: none; }
  .brand-name { font-weight: 600; color: var(--navy); white-space: nowrap; letter-spacing: .02em; }
  .brand-tag { position: absolute; color: #8a8a8a; text-transform: uppercase; letter-spacing: .08em; white-space: nowrap; }

  /* business card front */
  .card-front { left: 86px; top: 46px; width: 218px; height: 124px; background: #fff; }
  .card-front .brand { left: 15px; top: 23px; gap: 4px; }
  .card-front .brand-dot { width: 9px; height: 9px; }
  .card-front .brand-name { font-size: 6.6px; }
  .card-front .brand-tag { left: 28px; top: 36px; font-size: 3.4px; }
  .card-front .address { position: absolute; left: 15px; top: 62px; font-size: 5.6px; line-height: 8px; }
  .card-front .contacts { position: absolute; left: 15px; top: 81px; font-size: 5.6px; line-height: 8.4px; list-style: none; }
  .contacts li { display: flex; align-items: center; gap: 3px; }
  .contacts svg { width: 6px; height: 6px; fill: var(--navy); flex: none; }
  .card-front .person { position: absolute; right: 27px; top: 85px; text-align: right; }
  .person-name { font-size: 7px; font-weight: 600; color: var(--navy); white-space: nowrap; }
  .person-role { font-size: 5px; color: var(--red); margin-top: 1px; }

  /* business card back */
  .card-back { left: 338px; top: 46px; width: 218px; height: 124px; background: var(--navy); }
  .card-back .brand { left: 0; right: 0; top: 50px; justify-content: center; }
  .card-back .brand-name { color: #fff; font-size: 11px; }
  .card-back .brand-dot { width: 12px; height: 12px; }
  .web-white { position: absolute; left: 0; right: 0; text-align: center; color: #fff; letter-spacing: .16em; }
  .card-back .web-white { top: 104px; font-size: 5.2px; }

  /* envelope front */
  .envelope-front { left: 62px; top: 202px; width: 561px; height: 255px; }
  .envelope-front .brand { left: 24px; top: 30px; }
  .envelope-front .brand-dot { width: 15px; height: 15px; }
  .envelope-front .brand-name { font-size: 14px; }
  .envelope-front .brand-tag { left: 45px; top: 53px; font-size: 4.5px; }
  .envelope-front .address { position: absolute; left: 24px; top: 217px; font-size: 9px; line-height: 11.5px; }

  /* envelope back */
  .envelope-back { left: 57px; top: 480px; width: 559px; height: 254px; }
  .envelope-back .brand { left: 0; right: 0; top: 38px; justify-content: center; }
  .envelope-back .brand-name { color: #fff; font-size: 11px; }
  .envelope-back .brand-dot { width: 12px; height: 12px; }
  .envelope-back .web-white { top: 69px; font-size: 7px; }

  /* letterhead */
  .letterhead { left: 643px; top: 32px; width: 497px; height: 702px; }
  .letterhead .brand { left: 31px; top: 54px; }
  .letterhead .brand-dot { width: 15px; height: 15px; }
  .letterhead .brand-name { font-size: 14px; }
  .letterhead .brand-tag { left: 52px; top: 77px; font-size: 4.5px; }
  .letterhead .contacts { position: absolute; left: 31px; top: 643px; font-size: 9px; line-height: 12.2px; list-style: none; }
  .letterhead .contacts svg { width: 8px; height: 8px; }
  .letterhead .address { position: absolute; right: 32px; top: 645px; text-align: right; font-size: 9px; line-height: 11.2px; }
  .letterhead .web { color: var(--navy); letter-spacing: .14em; }
</style>
</head>
<body>

<!-- Business card, front -->
<section class="piece card-front" aria-label="Business card front">
  <svg class="decor" viewBox="0 0 218 124" width="218" height="124" aria-hidden="true">
    <path d="M114 0C168 8 204 42 202 75C200 100 186 115 172 124H218V0Z" fill="var(--red)"/>
    <path d="M178 0C198 18 210 52 206 80C202 102 188 116 176 124H218V0Z" fill="var(--navy)" stroke="#fff" stroke-width="1.2"/>
  </svg>
  <div class="brand"><span class="brand-dot"></span><span class="brand-name">BRELLWICK PARTNERS, LLC</span></div>
  <div class="brand-tag">Financial Planning and Consulting</div>
  <p class="address">2210 Larkspur Avenue<br>Dunmore Falls, NY 11204</p>
  <ul class="contacts">
    <li><svg viewBox="0 0 10 10"><path d="M1 3Q5 0 9 3L8 5H6V4H4V5H2Z M2 6H8V9H2Z"/></svg>555 0142 2253</li>
    <li><svg viewBox="0 0 10 10"><path d="M3 1H7V4H3Z M1 4H9V8H1Z"/></svg>555 0187 3856</li>
    <li><svg viewBox="0 0 10 10"><path d="M1 2H9V8H1Z"/></svg>marcus@brellwick.com</li>
    <li><svg viewBox="0 0 10 10"><circle cx="5" cy="5" r="4"/></svg>www.brellwick.com</li>
  </ul>
  <div class="person">
    <div class="person-name">MARCUS HALE</div>
    <div class="person-role">PRESIDENT</div>
  </div>
</section>

<!-- Business card, back -->
<section class="piece card-back" aria-label="Business card back">
  <div class="brand"><span class="brand-dot"></span><span class="brand-name">BRELLWICK PARTNERS, LLC</span></div>
  <div class="web-white">www.brellwick.com</div>
</section>

<!-- Envelope, front -->
<section class="piece envelope-front" aria-label="Envelope front">
  <svg class="decor" viewBox="0 0 561 255" width="561" height="255" aria-hidden="true">
    <path d="M350 0C450 12 540 60 561 138V0Z" fill="var(--red)"/>
    <path d="M432 0C500 22 548 72 561 128V0Z" fill="var(--navy)" stroke="#fff" stroke-width="1.5"/>
  </svg>
  <div class="brand"><span class="brand-dot"></span><span class="brand-name">BRELLWICK PARTNERS, LLC</span></div>
  <div class="brand-tag">Financial Planning and Consulting</div>
  <p class="address">2210 Larkspur Avenue<br>Dunmore Falls, NY 11204</p>
</section>

<!-- Envelope, back -->
<section class="piece envelope-back" aria-label="Envelope back">
  <svg class="decor" viewBox="0 0 559 254" width="559" height="254" aria-hidden="true">
    <path d="M0 0H559L548 70Q545 94 520 94H40Q14 94 11 70Z" fill="var(--navy)"/>
  </svg>
  <div class="brand"><span class="brand-dot"></span><span class="brand-name">BRELLWICK PARTNERS, LLC</span></div>
  <div class="web-white">www.brellwick.com</div>
</section>

<!-- Letterhead -->
<section class="piece letterhead" aria-label="Letterhead">
  <svg class="decor" viewBox="0 0 497 702" width="497" height="702" aria-hidden="true">
    <path d="M285 0C392 14 482 72 497 140V0Z" fill="var(--red)"/>
    <path d="M372 0C432 20 484 70 497 124V0Z" fill="var(--navy)" stroke="#fff" stroke-width="1.5"/>
  </svg>
  <div class="brand"><span class="brand-dot"></span><span class="brand-name">BRELLWICK PARTNERS, LLC</span></div>
  <div class="brand-tag">Financial Planning and Consulting</div>
  <ul class="contacts">
    <li><svg viewBox="0 0 10 10"><path d="M1 3Q5 0 9 3L8 5H6V4H4V5H2Z M2 6H8V9H2Z"/></svg>555 0142 2253</li>
    <li><svg viewBox="0 0 10 10"><path d="M3 1H7V4H3Z M1 4H9V8H1Z"/></svg>555 0187 3856</li>
    <li><svg viewBox="0 0 10 10"><path d="M1 2H9V8H1Z"/></svg>marcus@brellwick.com</li>
  </ul>
  <p class="address">2210 Larkspur Avenue<br>Dunmore Falls, NY 11204<br><span class="web">www.brellwick.com</span></p>
</section>

</body>
</html>
```